We are a building company that build new homes and units we are looking for something fresh and looks good my company name is
Lark Building Co Pty Ltd

Industry/Entity Type

Building

Contact Information for Business Card

Name Marco Ellis-Dunford
Tittle: Director
Address 14 Corrin St. Pelham Vale Vic 3179
Ph: 03 9582 4063
Mobile : 0400 362 918

www.larkbuildingco.com.au
Email: sales@larkbuildingco.com.au

```html
<!DOCTYPE html>
<html lang="en">
<head>
<meta charset="utf-8">
<title>Lark Building Co Pty Ltd – Business Card</title>
<link rel="stylesheet" href="https://fonts.googleapis.com/css2?family=Open+Sans:wght@400;600;700&display=swap">
<style>
  :root {
    --brand-blue: #1f72bd;
    --card-white: #ffffff;
    --card-black: #0b0b0b;
    --logo-grey: #7a7d80;
    --text-white: #ffffff;
    --page-bg: #e6e7e9;
  }
  * { box-sizing: border-box; margin: 0; padding: 0; }
  html, body {
    width: 1200px; height: 900px; overflow: hidden;
    background: var(--page-bg);
    font-family: "Open Sans", Arial, sans-serif;
  }
  .canvas {
    width: 1200px; height: 900px;
    display: flex; flex-direction: column;
    align-items: center; justify-content: center; gap: 30px;
  }
  .card {
    width: 720px; height: 411px;
    position: relative; overflow: hidden;
    box-shadow: 0 6px 18px rgba(0,0,0,0.18);
  }

  /* Back side */
  .card-back { background: var(--card-black); }
  .card-back .wordmark {
    position: absolute; left: 0; right: 0; top: 170px;
    display: flex; align-items: center; justify-content: center; gap: 12px;
  }
  .card-back .wordmark-mark {
    width: 18px; height: 18px; background: var(--brand-blue);
  }
  .card-back .wordmark-name {
    color: var(--text-white); font-weight: 600; font-size: 30px; letter-spacing: 0.3px;
  }
  .card-back .web {
    position: absolute; left: 0; right: 0; top: 222px; text-align: center;
    color: var(--brand-blue); font-size: 15px;
  }

  /* Front side */
  .card-front { background: var(--card-white); }
  .card-front .info-panel {
    position: absolute; top: 0; bottom: 0; left: 340px; right: 30px;
    background: var(--brand-blue);
    clip-path: polygon(0 0, 100% 0, 100% 100%, 0 100%, 0 22%, 12px 19%, 0 16%);
  }
  .card-front .wordmark {
    position: absolute; left: 40px; top: 186px; width: 280px;
    display: flex; align-items: center; gap: 10px;
  }
  .card-front .wordmark-mark {
    width: 16px; height: 16px; background: var(--brand-blue); flex: none;
  }
  .card-front .wordmark-name {
    color: var(--logo-grey); font-weight: 700; font-size: 21px; white-space: nowrap;
  }
  .contact {
    position: absolute; left: 372px; top: 58px; right: 40px;
    color: var(--text-white);
  }
  .contact .person-name { font-size: 23px; font-weight: 400; line-height: 1.2; }
  .contact .person-title { font-size: 15px; margin-top: 2px; }
  .contact .details { list-style: none; margin-top: 34px; }
  .contact .details li {
    display: flex; align-items: flex-start; gap: 14px;
    font-size: 16.5px; line-height: 1.3; margin-bottom: 12px;
  }
  .contact .details svg { width: 16px; height: 16px; flex: none; margin-top: 3px; fill: var(--text-white); }
  .contact .details .web-row { font-weight: 700; }
</style>
</head>
<body>
<main class="canvas">

  <section class="card card-back" aria-label="Business card back">
    <div class="wordmark">
      <span class="wordmark-mark"></span>
      <span class="wordmark-name">Lark Building Co Pty Ltd</span>
    </div>
    <p class="web">www.larkbuildingco.com.au</p>
  </section>

  <section class="card card-front" aria-label="Business card front">
    <div class="wordmark">
      <span class="wordmark-mark"></span>
      <span class="wordmark-name">Lark Building Co Pty Ltd</span>
    </div>

    <div class="info-panel"></div>

    <div class="contact">
      <p class="person-name">Marco Ellis-Dunford</p>
      <p class="person-title">Director</p>
      <ul class="details">
        <li>
          <svg viewBox="0 0 16 16" aria-hidden="true"><path d="M8 0a5.5 5.5 0 0 0-5.5 5.5C2.5 9.6 8 16 8 16s5.5-6.4 5.5-10.5A5.5 5.5 0 0 0 8 0zm0 8a2.4 2.4 0 1 1 0-4.8A2.4 2.4 0 0 1 8 8z"/></svg>
          <span>14 Corrin St. Pelham Vale<br>Vic 3179</span>
        </li>
        <li>
          <svg viewBox="0 0 16 16" aria-hidden="true"><path d="M3.6 1 6 3.8 4.7 5.6c.9 2 2.7 3.8 4.7 4.7L11.2 9 14 11.4 12.6 14C7 14 2 9 2 3.4z"/></svg>
          <span>03 9582 4063</span>
        </li>
        <li>
          <svg viewBox="0 0 16 16" aria-hidden="true"><path d="M4 0h8a1 1 0 0 1 1 1v14a1 1 0 0 1-1 1H4a1 1 0 0 1-1-1V1a1 1 0 0 1 1-1zm1 2v10h6V2zm3 11a1 1 0 1 0 0 2 1 1 0 0 0 0-2z"/></svg>
          <span>0400 362 918</span>
        </li>
        <li>
          <svg viewBox="0 0 16 16" aria-hidden="true"><path d="M1 3h14v1.2L8 9 1 4.2zm0 2.6 7 4.8 7-4.8V13H1z"/></svg>
          <span>sales@larkbuildingco.com.au</span>
        </li>
        <li class="web-row">
          <svg viewBox="0 0 16 16" aria-hidden="true"><path d="M8 0a8 8 0 1 0 0 16A8 8 0 0 0 8 0zm5.9 7.2h-2.6a12 12 0 0 0-1-5 6.4 6.4 0 0 1 3.6 5zM8 1.7c.7.9 1.5 2.8 1.7 5.5H6.3C6.5 4.5 7.3 2.6 8 1.7zM5.7 2.2a12 12 0 0 0-1 5H2.1a6.4 6.4 0 0 1 3.6-5zM2.1 8.8h2.6a12 12 0 0 0 1 5 6.4 6.4 0 0 1-3.6-5zM8 14.3c-.7-.9-1.5-2.8-1.7-5.5h3.4c-.2 2.7-1 4.6-1.7 5.5zm2.3-.5a12 12 0 0 0 1-5h2.6a6.4 6.4 0 0 1-3.6 5z"/></svg>
          <span>www.larkbuildingco.com.au</span>
        </li>
      </ul>
    </div>
  </section>

</main>
</body>
</html>
```